Business Card Design Project 4thKVL

Business card that looks professional but stands out!

Industry/Entity Type

Business

Requirements
Must have
• Tailor to Realtors
loan products on the back of the card

```html
<!DOCTYPE html>
<html lang="en">
<head>
<meta charset="utf-8">
<title>4thKVL Mortgage – Business Card</title>
<link rel="stylesheet" href="https://fonts.googleapis.com/css2?family=Arimo:wght@400;700&display=swap">
<style>
  :root {
    --bg: #2b2b2b;
    --card-white: #ffffff;
    --brand-blue: #0a4c99;
    --brand-blue-light: #2a66b3;
    --panel-grey: #8f8f8f;
    --rule-grey: #9a9a9a;
    --text-grey: #6d6d6d;
    --text-white: #ffffff;
  }
  * { box-sizing: border-box; margin: 0; padding: 0; }
  html, body { width: 1200px; height: 900px; overflow: hidden; }
  body {
    background: var(--bg);
    font-family: "Arimo", Arial, sans-serif;
    position: relative;
  }
  .card {
    position: absolute;
    top: 302px;
    width: 520px;
    height: 297px;
    background: var(--card-white);
    overflow: hidden;
    box-shadow: 0 10px 24px rgba(0,0,0,.45);
  }
  .card--front { left: 60px; }
  .card--back  { left: 620px; }

  /* Front */
  .brand {
    position: absolute;
    top: 34px;
    left: 150px;
    display: flex;
    align-items: center;
    gap: 12px;
  }
  .brand__mark {
    width: 44px;
    height: 44px;
    background: var(--brand-blue);
  }
  .brand__name {
    color: var(--brand-blue);
    font-weight: 700;
    font-size: 27px;
    letter-spacing: .5px;
  }
  .tagline {
    position: absolute;
    top: 100px;
    left: 56px;
    right: 40px;
    color: var(--text-grey);
    font-size: 11px;
    line-height: 14px;
    text-align: center;
  }
  .band {
    position: absolute;
    left: 0; right: 0; bottom: 0;
    height: 150px;
    background: var(--brand-blue);
    border-top: 5px solid var(--rule-grey);
  }
  .person {
    position: absolute;
    left: 26px;
    top: 62px;
    color: var(--text-white);
  }
  .person__name { font-size: 20px; font-weight: 700; }
  .person__title { font-size: 12px; margin-top: 2px; }
  .person__address {
    display: flex;
    gap: 8px;
    margin-top: 8px;
    font-size: 11px;
    line-height: 14px;
  }
  .contacts {
    position: absolute;
    right: 36px;
    top: 16px;
    list-style: none;
    color: var(--text-white);
    font-size: 11.5px;
  }
  .contacts li {
    display: flex;
    align-items: center;
    gap: 8px;
    height: 19px;
  }
  .icon { width: 12px; height: 12px; flex: none; fill: var(--text-white); }

  /* Back */
  .programs-panel {
    position: absolute;
    top: 0; bottom: 0; right: 0;
    width: 318px;
    background: var(--panel-grey);
  }
  .programs-accent {
    position: absolute;
    left: 196px;
    top: 52px;
    width: 7px;
    height: 180px;
    background: var(--brand-blue);
  }
  .programs {
    position: absolute;
    left: 222px;
    top: 40px;
    right: 14px;
    color: var(--text-white);
  }
  .programs__title {
    font-size: 14px;
    font-weight: 700;
    letter-spacing: .5px;
    margin-bottom: 4px;
  }
  .programs__cols { display: flex; gap: 20px; }
  .programs__list {
    list-style: none;
    font-size: 11px;
    line-height: 14.5px;
  }
  .programs__list li::before {
    content: "•";
    margin: 0 7px 0 5px;
  }
  .programs__list--second { margin-top: -18px; }
</style>
</head>
<body>

<section class="card card--front" aria-label="Business card front">
  <div class="brand">
    <span class="brand__mark"></span>
    <span class="brand__name">4thKVL Mortgage</span>
  </div>
  <p class="tagline">We make the journey of buying a home or refinancing a mortgage easy.<br>You can depend on us to help you find the perfect loan program for you.</p>

  <div class="band">
    <ul class="contacts">
      <li><svg class="icon" viewBox="0 0 12 12"><path d="M2.5 0.5l2 2.5-1.2 1.3c.7 1.6 2 2.9 3.4 3.5L8 6.6l2.5 2-1.2 2.4C4.8 10.6 1.3 7 .9 2.2z"/></svg>555.210.4080</li>
      <li><svg class="icon" viewBox="0 0 12 12"><rect x="3" y="0.5" width="6" height="3.5"/><rect x="0.5" y="4.5" width="11" height="5" rx="1"/><rect x="3" y="8" width="6" height="3.5"/></svg>555.210.4081</li>
      <li><svg class="icon" viewBox="0 0 12 12"><path d="M0.5 2.5h11v7h-11z"/><path d="M0.5 2.5l5.5 4 5.5-4" fill="none" stroke="#0a4c99" stroke-width="1"/></svg>info@4thkvl.com</li>
      <li><svg class="icon" viewBox="0 0 12 12"><circle cx="6" cy="6" r="5.5"/><path d="M.5 6h11M6 .5c-2.5 3-2.5 8 0 11M6 .5c2.5 3 2.5 8 0 11" fill="none" stroke="#0a4c99" stroke-width=".9"/></svg>www.4thkvl.com</li>
    </ul>

    <div class="person">
      <h1 class="person__name">Dana Whitfield</h1>
      <p class="person__title">Manager</p>
      <p class="person__address">
        <svg class="icon" viewBox="0 0 12 12"><path d="M6 .5a4 4 0 0 0-4 4c0 3 4 7 4 7s4-4 4-7a4 4 0 0 0-4-4zm0 2.2a1.8 1.8 0 1 1 0 3.6 1.8 1.8 0 0 1 0-3.6z"/></svg>
        <span>Address 48 Harbor Lane, Suite 210<br>Fairview CA 12345</span>
      </p>
    </div>
  </div>
</section>

<section class="card card--back" aria-label="Business card back">
  <div class="programs-panel"></div>
  <div class="programs-accent"></div>
  <div class="programs">
    <h2 class="programs__title">LOAN PROGRAMS</h2>
    <div class="programs__cols">
      <ul class="programs__list">
        <li>Jumbo Mortgages</li>
        <li>30 Year Fixed</li>
        <li>15 Year Fixed</li>
        <li>FHA Home Loan</li>
        <li>VA 30 Year Fixed</li>
        <li>HARP 2.0</li>
        <li>Reverse Mortgages</li>
        <li>FHA Home Loan</li>
        <li>VA 30 Year Fixed</li>
        <li>HARP 2.0</li>
        <li>Reverse Mortgages</li>
      </ul>
      <ul class="programs__list programs__list--second">
        <li>Jumbo Mortgages</li>
        <li>30 Year Fixed</li>
        <li>15 Year Fixed</li>
        <li>FHA Home Loan</li>
        <li>VA 30 Year Fixed</li>
        <li>HARP 2.0</li>
        <li>Reverse Mortgages</li>
        <li>FHA Home Loan</li>
        <li>VA 30 Year Fixed</li>
        <li>HARP 2.0</li>
        <li>Reverse Mortgages</li>
      </ul>
    </div>
  </div>
</section>

</body>
</html>
```